Business Card Design Project

Business Card
We are rebranding with a new logo
Industry/Entity Type
Business
Contact Information for Business Card
Dennis Morvale +61 487215963 dennis@quorv.com.au P.O. Box 872 Fernlow QLD 4309
Requirements
Must have
- Logo

```html
<!DOCTYPE html>
<html lang="en">
<head>
<meta charset="utf-8">
<title>Quorv International – Business Card</title>
<link rel="stylesheet" href="https://fonts.googleapis.com/css2?family=Lato:wght@400;700&family=Arimo:wght@400&display=swap">
<style>
  :root {
    --backdrop: #e6e7e8;
    --card: #ffffff;
    --accent: #6ac8ef;
    --ink: #1c1c1c;
    --ink-soft: #4a4a4a;
    --brand: #1f6fa3;
  }
  * { margin: 0; padding: 0; box-sizing: border-box; }
  html, body {
    width: 1200px; height: 1000px; overflow: hidden;
    background: var(--backdrop);
  }
  .canvas {
    position: relative; width: 1200px; height: 1000px;
  }
  .card {
    position: absolute; left: 75px; top: 200px;
    width: 1050px; height: 600px;
    background: var(--card);
    box-shadow: 6px 8px 14px rgba(0,0,0,0.28);
    overflow: hidden;
  }
  .card__name {
    position: absolute; left: 73px; top: 60px;
    font-family: "Lato", sans-serif; font-size: 40px;
    letter-spacing: 1px; color: var(--ink); font-weight: 400;
  }
  .card__name strong { font-weight: 700; }
  .brand {
    position: absolute; right: 65px; top: 78px;
    display: flex; align-items: center; gap: 14px;
  }
  .brand__dot {
    width: 26px; height: 26px; border-radius: 50%;
    background: var(--accent);
  }
  .brand__name {
    font-family: "Lato", sans-serif; font-weight: 700;
    font-size: 34px; letter-spacing: 2px; color: var(--brand);
    text-transform: uppercase;
  }
  .card__rule {
    position: absolute; left: 0; right: 0; top: 412px;
    height: 4px; background: var(--accent);
  }
  .contact-icon {
    position: absolute; top: 390px;
    width: 48px; height: 48px;
  }
  .contact-icon--phone { left: 130px; }
  .contact-icon--mail { left: 491px; }
  .contact-icon--web { left: 827px; }
  .contact {
    position: absolute;
    font-family: "Arimo", sans-serif; font-size: 21px;
    letter-spacing: 1.6px; color: var(--ink-soft);
    line-height: 38px; white-space: nowrap;
  }
  .contact--phone { left: 72px; top: 464px; }
  .contact--mail { left: 395px; top: 460px; }
  .contact--address { left: 735px; top: 460px; text-align: center; width: 240px; }
  .card__band {
    position: absolute; left: 0; right: 0; bottom: 0;
    height: 40px; background: var(--accent);
  }
</style>
</head>
<body>
<div class="canvas">
  <article class="card">
    <h1 class="card__name"><strong>Dennis</strong> Morvale</h1>

    <div class="brand">
      <span class="brand__dot"></span>
      <span class="brand__name">Quorv International</span>
    </div>

    <div class="card__rule"></div>

    <svg class="contact-icon contact-icon--phone" viewBox="0 0 48 48" aria-hidden="true">
      <circle cx="24" cy="24" r="24" fill="var(--accent)"/>
      <path d="M17 13c1-1 2.5-1 3.3.2l2.3 3.4c.6 1 .4 2.2-.5 2.9l-1.5 1.2c1 2.6 3 4.7 5.6 5.8l1.2-1.5c.7-.9 2-1.1 2.9-.5l3.4 2.3c1.2.8 1.2 2.3.2 3.3l-1.8 1.8c-1.2 1.2-3 1.5-4.5.8C21 30.3 17.7 27 15.3 20.6c-.7-1.5-.4-3.3.8-4.5z" fill="#fff"/>
    </svg>
    <svg class="contact-icon contact-icon--mail" viewBox="0 0 48 48" aria-hidden="true">
      <circle cx="24" cy="24" r="24" fill="var(--accent)"/>
      <rect x="13" y="16" width="22" height="16" rx="1.5" fill="#fff"/>
      <path d="M13.5 16.8 24 25l10.5-8.2" fill="none" stroke="var(--accent)" stroke-width="1.8"/>
    </svg>
    <svg class="contact-icon contact-icon--web" viewBox="0 0 48 48" aria-hidden="true">
      <circle cx="24" cy="24" r="24" fill="var(--accent)"/>
      <g fill="none" stroke="#fff" stroke-width="1.8">
        <circle cx="24" cy="24" r="12"/>
        <ellipse cx="24" cy="24" rx="5.5" ry="12"/>
        <line x1="12" y1="24" x2="36" y2="24"/>
        <line x1="24" y1="12" x2="24" y2="36"/>
        <path d="M14 18h20M14 30h20"/>
      </g>
    </svg>

    <p class="contact contact--phone">+61&nbsp; 487215963</p>
    <p class="contact contact--mail">dennis@quorv.com.au</p>
    <p class="contact contact--address">P.O.&nbsp; Box&nbsp; 872<br>Fernlow&nbsp; QLD&nbsp; 4309</p>

    <div class="card__band"></div>
  </article>
</div>
</body>
</html>
```